Pine Hollow Haven Home Inc. Website Update

We have a couple of broken links such as the "contact us" and would like to add board members and a calendar of events. We are open to a new design.

```html
<!DOCTYPE html>
<html lang="en">
<head>
<meta charset="utf-8">
<title>Pine Hollow Haven Home</title>
<link rel="stylesheet" href="https://fonts.googleapis.com/css2?family=Cinzel:wght@400;700&family=Open+Sans:wght@400;600;700&display=swap">
<style>
:root{
  --pink:#d9547a;
  --pink-dark:#c2406a;
  --blue:#1f5aa8;
  --navy:#2b2f74;
  --band:#1c58b0;
  --ink:#222;
  --muted:#555;
  --line:#e3e3e3;
  --white:#fff;
}
*{margin:0;padding:0;box-sizing:border-box}
html,body{width:1200px;height:3593px;overflow:hidden;background:var(--white)}
body{font-family:"Open Sans",Arial,sans-serif;color:var(--ink);position:relative}
.abs{position:absolute}
.decor{position:absolute;left:0;top:0;width:1200px;height:3593px}
.hero-photo{position:absolute;left:0;top:0;width:1200px;height:840px;
  background:linear-gradient(100deg,#6f7f58 0%,#a39a78 35%,#caa79a 60%,#b5525a 82%,#7d3a40 100%)}
.topbar{position:absolute;left:0;top:0;width:1200px;height:10px;background:var(--pink)}
.header{position:absolute;left:144px;top:0;width:910px;height:163px;background:var(--white);
  border-radius:0 0 14px 14px;box-shadow:0 4px 14px rgba(0,0,0,.15)}
.brand{position:absolute;left:26px;top:40px;display:flex;align-items:center;gap:12px;width:230px}
.brand-dot{width:44px;height:44px;border-radius:50%;background:var(--pink);flex:none}
.brand-name{font-family:"Cinzel",serif;font-weight:700;color:var(--pink);font-size:19px;line-height:1.2}
.nav{position:absolute;left:251px;top:38px;display:flex;gap:17px;font-size:14px;color:#333}
.nav .active{color:var(--pink)}
.pill{position:absolute;height:44px;border-radius:22px;font-size:14px;font-weight:700;
  display:flex;align-items:center;justify-content:center;text-transform:uppercase}
.pill-outline-pink{border:2px solid var(--pink);color:var(--pink);background:var(--white)}
.pill-blue{background:var(--blue);color:var(--white)}
.pill-pink{background:var(--pink);color:var(--white)}
.pill-outline-white{border:2px solid var(--white);color:var(--white)}
.social{position:absolute;width:32px;height:32px;border-radius:50%}
.hero-title{position:absolute;left:143px;top:345px;font-family:"Cinzel",serif;font-weight:700;
  font-size:60px;line-height:72px;color:var(--white);text-transform:uppercase}
.dots{position:absolute;left:143px;top:667px;display:flex;gap:8px}
.dots span{width:10px;height:10px;border-radius:50%;background:rgba(255,255,255,.6)}
.dots span.on{background:var(--white)}
.about-card{position:absolute;left:144px;top:730px;width:910px;height:407px;background:var(--white);
  border-radius:14px;box-shadow:0 2px 14px rgba(0,0,0,.2)}
.about-photo{position:absolute;left:19px;top:12px;width:364px;height:324px;border-radius:10px;
  background:linear-gradient(120deg,#e8e0d8,#c7b8a8 45%,#b24b4e 80%,#3b3030)}
.badge{position:absolute;left:139px;top:262px;width:124px;height:124px;border-radius:50%;background:#d7a932}
.section-title{font-family:"Cinzel",serif;color:var(--pink);font-size:36px;text-transform:uppercase;letter-spacing:1px}
.divider{position:absolute;width:60px;height:8px}
.about-title{position:absolute;left:443px;top:40px}
.about-text{position:absolute;left:443px;top:122px;width:440px;font-size:13px;line-height:29px;color:var(--muted)}
.read-more{position:absolute;left:455px;top:312px;width:160px;height:40px;background:var(--pink);color:var(--white);
  font-size:13px;font-weight:700;display:flex;align-items:center;justify-content:center;gap:8px}
.center{text-align:center;position:absolute;left:0;width:1200px}
.board-sub{top:1295px;font-size:16px;line-height:30px;color:#444}
.member{position:absolute;width:200px;text-align:center}
.member-photo{width:180px;height:180px;border-radius:50%;margin:0 auto;
  background:radial-gradient(circle at 50% 40%,#d9b8a3,#8a6a5a 70%,#5a4f4f)}
.member-photo.ring{border:5px solid var(--blue)}
.member-name{font-size:18px;font-weight:600;text-transform:uppercase;margin-top:18px;color:#222}
.member-role{font-size:12px;color:var(--pink);margin-top:2px}
.member-social{display:flex;justify-content:center;gap:6px;margin-top:8px}
.member-social span{width:16px;height:16px;border-radius:50%}
.arrow{position:absolute;top:1505px;width:40px;height:64px}
.we-title{top:1968px;font-family:"Cinzel",serif;font-size:36px;color:var(--white)}
.we-sub{top:2036px;font-size:17px;line-height:31px;color:var(--white)}
.hub{position:absolute;left:443px;top:2191px;width:312px;height:312px;border-radius:50%;
  background:var(--white);border:14px solid #d8d8e4;display:flex;align-items:center;justify-content:center}
.hub-inner{width:240px;height:240px;border-radius:50%;background:var(--pink);display:flex;align-items:center;
  justify-content:center;text-align:center;font-family:"Cinzel",serif;font-weight:700;color:var(--white);font-size:22px;line-height:1.3;padding:20px}
.hub-dot{position:absolute;width:18px;height:18px;border-radius:50%;border:3px solid var(--white)}
.svc-icon{position:absolute;width:84px;height:84px;border-radius:50%;background:var(--white);
  display:flex;align-items:center;justify-content:center}
.svc-icon.pink{border:8px solid var(--pink)}
.svc-icon.blue{border:8px solid var(--blue)}
.svc-label{position:absolute;color:var(--white);font-size:17px;font-weight:600;line-height:30px}
.cal-title{top:2705px}
.event-card{position:absolute;left:144px;top:2833px;width:910px;height:419px;background:var(--white);
  border-radius:14px;box-shadow:0 2px 14px rgba(0,0,0,.2)}
.event-brand{position:absolute;left:40px;top:48px;display:flex;align-items:center;gap:10px}
.event-brand .brand-dot{width:30px;height:30px}
.event-brand .brand-name{font-size:15px}
.event-title{position:absolute;left:40px;top:166px;width:300px;font-size:21px;font-weight:600;line-height:30px;color:#222}
.event-text{position:absolute;left:40px;top:236px;width:360px;font-size:12px;line-height:24px;color:var(--muted)}
.event-meta{position:absolute;left:40px;top:335px;font-size:12px;color:#444;display:flex;gap:14px;align-items:center}
.event-nav{position:absolute;top:352px;width:28px;height:28px;border-radius:50%;border:1px solid #999}
.calendar{position:absolute;left:491px;top:12px;width:407px;height:395px;border:1px solid var(--line)}
.cal-head{height:65px;background:var(--pink);color:var(--white);font-size:22px;font-weight:700;
  display:flex;align-items:center;justify-content:space-between;padding:0 22px}
.cal-grid{display:grid;grid-template-columns:repeat(7,1fr)}
.cal-grid div{height:55px;display:flex;align-items:center;justify-content:center;border-right:1px solid var(--line);
  border-bottom:1px solid var(--line);font-size:16px;font-weight:600;color:#222;position:relative}
.cal-grid .dow{height:40px;font-size:13px;font-weight:400;color:#555}
.cal-grid .off{color:#aaa;font-weight:400}
.cal-grid .today span{width:40px;height:40px;border-radius:50%;background:var(--blue);color:var(--white);
  display:flex;align-items:center;justify-content:center}
.cal-grid .mark::after{content:"";position:absolute;bottom:8px;width:4px;height:4px;border-radius:50%;background:#555}
.contact{position:absolute;top:3318px;display:flex;align-items:center;gap:16px;color:var(--white);font-size:14px;line-height:21px}
.contact-icon{width:46px;height:46px;border-radius:50%;border:2px solid var(--white);display:flex;align-items:center;justify-content:center;flex:none}
.foot-nav{top:3456px;font-size:15px;color:var(--white);text-transform:uppercase;word-spacing:2px}
.foot-nav span{margin:0 10px}
.copyright{top:3496px;font-size:11px;color:var(--white)}
.foot-social{position:absolute;left:554px;top:3535px;display:flex;gap:8px}
.foot-social span{width:18px;height:18px;border-radius:50%;background:var(--white)}
</style>
</head>
<body>

<div class="hero-photo" role="img" aria-label="Photo of a smiling teenage girl outdoors with friends softly blurred behind her"></div>

<svg class="decor" viewBox="0 0 1200 3593" aria-hidden="true">
  <path d="M0,840 Q600,660 1200,840 L1200,1000 L0,1000 Z" fill="#fff"/>
  <path d="M0,840 Q600,660 1200,840" fill="none" stroke="#d9547a" stroke-width="5"/>
  <defs>
    <linearGradient id="blueSection" x1="0" y1="0" x2="1" y2="1">
      <stop offset="0" stop-color="#3a3a8c"/>
      <stop offset="0.55" stop-color="#2f3f96"/>
      <stop offset="1" stop-color="#1f55ab"/>
    </linearGradient>
  </defs>
  <path d="M0,1720 Q600,2016 1200,1720 L1200,2598 Q600,2792 0,2598 Z" fill="url(#blueSection)"/>
  <path d="M0,1720 Q600,2016 1200,1720" fill="none" stroke="#d9547a" stroke-width="5"/>
  <path d="M0,2598 Q600,2792 1200,2598" fill="none" stroke="#d9547a" stroke-width="5"/>
  <path d="M0,3080 Q600,3030 1200,3080 L1200,3593 L0,3593 Z" fill="#1c58b0"/>
</svg>

<div class="topbar"></div>

<header class="header">
  <div class="brand"><span class="brand-dot"></span><span class="brand-name">Pine Hollow Haven Home</span></div>
  <nav class="nav">
    <span class="active">Home</span><span>About</span><span>How You Can Help</span><span>Services Offered</span><span>Our Love of Pets</span><span>Contact Us</span><span>Angel Walk</span>
  </nav>
  <div class="pill pill-outline-pink" style="left:323px;top:96px;width:161px">Our Girls</div>
  <div class="pill pill-blue" style="left:495px;top:96px;width:161px">Our Mission</div>
  <span class="social" style="left:683px;top:102px;background:#3b5998"></span>
  <span class="social" style="left:723px;top:102px;background:#3ba6e6"></span>
  <span class="social" style="left:763px;top:102px;background:#dd4b39"></span>
  <span class="social" style="left:803px;top:102px;background:#0e76a8"></span>
  <span class="social" style="left:843px;top:102px;background:#e52d27"></span>
</header>

<h1 class="hero-title">Pine Hollow<br>Haven Home</h1>
<div class="pill pill-pink" style="left:143px;top:522px;width:159px;height:46px">Our Mission</div>
<div class="pill pill-outline-white" style="left:311px;top:522px;width:159px;height:46px">Our Girls</div>
<div class="dots"><span class="on"></span><span></span><span></span><span></span></div>

<section class="about-card">
  <div class="about-photo" role="img" aria-label="Photo of three girls laughing together on a couch"></div>
  <div class="badge"></div>
  <h2 class="section-title about-title">About Us</h2>
  <svg class="divider" style="left:445px;top:94px" viewBox="0 0 60 8"><path d="M0,5 Q30,-1 60,5" stroke="#1f5aa8" stroke-width="2" fill="none"/></svg>
  <p class="about-text">Pine Hollow Haven Home is home to 31 girls ranging in ages from 12-21. The home has seven bedrooms and four bathrooms with a large spa tub for relaxing. Our kitchen takes on the aroma of a restaurant in the evenings as the girls practice their Independent Living Skills with menu planning and preparation in a supervised setting.</p>
  <div class="read-more">READ MORE <svg width="12" height="12" viewBox="0 0 12 12"><circle cx="6" cy="6" r="6" fill="#fff"/><path d="M5,3 L8,6 L5,9" stroke="#d9547a" stroke-width="1.6" fill="none"/></svg></div>
</section>

<h2 class="section-title center" style="top:1230px">Board Members</h2>
<p class="center board-sub">Sed ut perspiciatis unde omnis iste natus error sit voluptntium doloremque laudantium<br>totam rem aperiarchitecto beatae vitae dicta sunt explicabo</p>
<svg class="divider" style="left:570px;top:1372px" viewBox="0 0 60 8"><path d="M0,5 Q30,-1 60,5" stroke="#1f5aa8" stroke-width="2" fill="none"/></svg>

<svg class="arrow" style="left:82px" viewBox="0 0 40 64"><path d="M32,4 L8,32 L32,60" stroke="#aaa" stroke-width="2" fill="none"/></svg>
<svg class="arrow" style="left:1078px" viewBox="0 0 40 64"><path d="M8,4 L32,32 L8,60" stroke="#aaa" stroke-width="2" fill="none"/></svg>

<div class="member" style="left:141px;top:1448px">
  <div class="member-photo" role="img" aria-label="Portrait photo of a board member"></div>
  <div class="member-name">Nora Pell</div><div class="member-role">CEO</div>
  <div class="member-social"><span style="background:#3b5998"></span><span style="background:#3ba6e6"></span><span style="background:#dd4b39"></span></div>
</div>
<div class="member" style="left:380px;top:1448px">
  <div class="member-photo ring" role="img" aria-label="Portrait photo of a board member"></div>
  <div class="member-name">Elena Marsh</div><div class="member-role">CEO</div>
  <div class="member-social"><span style="background:#3b5998"></span><span style="background:#3ba6e6"></span><span style="background:#dd4b39"></span></div>
</div>
<div class="member" style="left:619px;top:1448px">
  <div class="member-photo" role="img" aria-label="Portrait photo of a board member"></div>
  <div class="member-name">Talia Reyes</div><div class="member-role">CEO</div>
  <div class="member-social"><span style="background:#3b5998"></span><span style="background:#3ba6e6"></span><span style="background:#dd4b39"></span></div>
</div>
<div class="member" style="left:858px;top:1448px">
  <div class="member-photo" role="img" aria-label="Portrait photo of a board member"></div>
  <div class="member-name">Ivy Lund</div><div class="member-role">CEO</div>
  <div class="member-social"><span style="background:#3b5998"></span><span style="background:#3ba6e6"></span><span style="background:#dd4b39"></span></div>
</div>

<h2 class="center we-title">We are Pine Hollow Haven Home</h2>
<p class="center we-sub">With the help of our community, we have raised over 1000 girls and counting!<br>Some of the services we offer include:</p>

<div class="hub"><div class="hub-inner">Pine Hollow Haven Home Inc.</div></div>
<span class="hub-dot" style="left:464px;top:2249px;background:var(--pink)"></span>
<span class="hub-dot" style="left:716px;top:2249px;background:var(--blue)"></span>
<span class="hub-dot" style="left:464px;top:2425px;background:var(--blue)"></span>
<span class="hub-dot" style="left:716px;top:2425px;background:var(--pink)"></span>

<div class="svc-icon blue" style="left:150px;top:2216px">
  <svg width="40" height="40" viewBox="0 0 40 40"><rect x="6" y="8" width="6" height="26" fill="#d9547a"/><rect x="12" y="20" width="22" height="8" fill="#1f5aa8"/><rect x="28" y="14" width="6" height="20" fill="#d9547a"/></svg>
</div>
<div class="svc-label" style="left:256px;top:2229px">Room, Board, and<br>Watchful Oversight</div>

<div class="svc-icon pink" style="left:150px;top:2389px">
  <svg width="40" height="40" viewBox="0 0 40 40"><rect x="4" y="16" width="32" height="12" rx="3" fill="#1f5aa8"/><rect x="8" y="10" width="24" height="8" rx="2" fill="#d9547a"/><rect x="6" y="28" width="3" height="5" fill="#1f5aa8"/><rect x="31" y="28" width="3" height="5" fill="#1f5aa8"/></svg>
</div>
<div class="svc-label" style="left:256px;top:2400px">Transitional Living<br>Services</div>

<div class="svc-icon pink" style="left:964px;top:2216px">
  <svg width="40" height="40" viewBox="0 0 40 40"><rect x="8" y="6" width="24" height="28" fill="none" stroke="#1f5aa8" stroke-width="3"/><rect x="13" y="11" width="5" height="5" fill="#d9547a"/><rect x="22" y="11" width="5" height="5" fill="#d9547a"/><rect x="13" y="20" width="5" height="5" fill="#d9547a"/><rect x="22" y="20" width="5" height="5" fill="#d9547a"/></svg>
</div>
<div class="svc-label" style="right:254px;top:2229px;text-align:right">Independent Living<br>Services</div>

<div class="svc-icon blue" style="left:964px;top:2389px">
  <svg width="40" height="40" viewBox="0 0 40 40"><rect x="7" y="16" width="26" height="18" fill="none" stroke="#d9547a" stroke-width="3"/><rect x="5" y="11" width="30" height="6" fill="#d9547a"/><rect x="18" y="11" width="4" height="23" fill="#1f5aa8"/></svg>
</div>
<div class="svc-label" style="right:254px;top:2416px;text-align:right">Foster Gift Shop</div>

<h2 class="section-title center cal-title">Calendar of Events</h2>
<svg class="divider" style="left:570px;top:2768px" viewBox="0 0 60 8"><path d="M0,5 Q30,-1 60,5" stroke="#1f5aa8" stroke-width="2" fill="none"/></svg>

<section class="event-card">
  <div class="event-brand"><span class="brand-dot"></span><span class="brand-name">Pine Hollow Haven Home</span></div>
  <h3 class="event-title">Lorem ipsum dolor sit amet, consecing elit</h3>
  <p class="event-text">Sed ut perspiciatis unde omnis iste natus error sit voluptatem accusantium doloremque laudantium, totam rem aperiam, eaque ipsa quae ab illo inventore verite.</p>
  <div class="event-meta">
    <span><svg width="11" height="11" viewBox="0 0 11 11"><rect x="0.5" y="1.5" width="10" height="9" fill="none" stroke="#1f5aa8"/><line x1="0.5" y1="4" x2="10.5" y2="4" stroke="#1f5aa8"/></svg> March 15,2019</span>
    <span style="color:#1f5aa8">&#9825;</span><span style="margin-left:-10px">2</span>
    <span style="color:#1f5aa8">&#9675;</span><span style="margin-left:-10px">4</span>
  </div>
  <svg class="event-nav" style="left:378px" viewBox="0 0 28 28"><path d="M16,9 L11,14 L16,19" stroke="#666" stroke-width="1.5" fill="none"/></svg>
  <svg class="event-nav" style="left:414px" viewBox="0 0 28 28"><path d="M12,9 L17,14 L12,19" stroke="#666" stroke-width="1.5" fill="none"/></svg>

  <div class="calendar">
    <div class="cal-head"><span>&#8249;</span><span>March 2019</span><span>&#8250;</span></div>
    <div class="cal-grid">
      <div class="dow">MON</div><div class="dow">TUE</div><div class="dow">WED</div><div class="dow">THU</div><div class="dow">FRI</div><div class="dow">SAT</div><div class="dow">SUN</div>
      <div class="off mark">30</div><div>1</div><div>2</div><div>3</div><div>4</div><div>5</div><div>6</div>
      <div>7</div><div>8</div><div>9</div><div>10</div><div>11</div><div>12</div><div>13</div>
      <div>14</div><div class="today"><span>15</span></div><div>16</div><div>17</div><div>18</div><div>19</div><div>20</div>
      <div class="mark">21</div><div>22</div><div>23</div><div>24</div><div>25</div><div>26</div><div>27</div>
      <div>28</div><div>29</div><div>30</div><div>31</div><div class="off">1</div><div class="off">2</div><div class="off">3</div>
    </div>
  </div>
</section>

<div class="contact" style="left:142px">
  <span class="contact-icon"><svg width="22" height="22" viewBox="0 0 22 22"><path d="M2,11 L11,3 L20,11 L17,11 L17,19 L5,19 L5,11 Z" fill="#fff"/></svg></span>
  <span>418 Cedar Ridge Ln, Alder,<br>GA 30000, USA</span>
</div>
<div class="contact" style="left:420px">
  <span class="contact-icon"><svg width="22" height="22" viewBox="0 0 22 22"><path d="M5,3 L9,3 L10,8 L7.5,9.5 Q9.5,13.5 12.5,14.5 L14,12 L19,13 L19,17 Q11,19 5,9 Z" fill="#fff"/></svg></span>
  <span>555.014.2207</span>
</div>
<div class="contact" style="left:612px">
  <span class="contact-icon"><svg width="22" height="22" viewBox="0 0 22 22"><rect x="3" y="5" width="16" height="12" fill="#fff"/><path d="M3,5 L11,12 L19,5" stroke="#1c58b0" stroke-width="1.5" fill="none"/></svg></span>
  <span>hello@pinehollowhaven.org</span>
</div>
<div class="contact" style="left:854px">
  <span class="contact-icon"><svg width="22" height="22" viewBox="0 0 22 22"><circle cx="11" cy="11" r="8" fill="none" stroke="#fff" stroke-width="2"/><path d="M11,6 L11,11 L15,13" stroke="#fff" stroke-width="2" fill="none"/></svg></span>
  <span>WINGS<br>7:36 pm - April 26, 2018</span>
</div>

<nav class="center foot-nav">Home<span>/</span>About<span>/</span>How You Can Help<span>/</span>Services Offered<span>/</span>Our Love of Pets<span>/</span>Contact Us<span>/</span>Angel Walk</nav>
<p class="center copyright">Copyright 2019 © Companyname All Rights Reserved &nbsp;|&nbsp; Privacy policy</p>
<div class="foot-social"><span></span><span></span><span></span><span></span></div>

</body>
</html>
```